Packaging design for a reclosable bag for our product

We have a logo, and we need to put it on packaging for our product and while we want the look to be simple, we want it to follow good design principles and also contain spaces for other product descriptions.

There will be 5 sizes at launch so I'd like 5 variations, one for each size.

I've included a few mockups of the type of bag that I made but they are all just rough ideas that I had.

I want the brand to look scientific and methodical and even a bit quirky, as in "wow this is a serious product but also a bit unusual."

```html
<!DOCTYPE html>
<html lang="en">
<head>
<meta charset="utf-8">
<title>Lumetric Bias Lighting – Extra Large Bag</title>
<link rel="stylesheet" href="https://fonts.googleapis.com/css2?family=Montserrat:wght@500;700&display=swap">
<style>
  :root {
    --backdrop: #d9d9d9;
    --bag: #050505;
    --ink: #f2f2f2;
  }
  html, body {
    margin: 0;
    padding: 0;
    width: 1200px;
    height: 960px;
    overflow: hidden;
    background: var(--backdrop);
  }
  .canvas {
    position: relative;
    width: 1200px;
    height: 960px;
  }
  .bag {
    position: absolute;
    left: 250px;
    top: 70px;
    width: 700px;
    height: 820px;
    background: var(--bag);
    color: var(--ink);
    font-family: "Montserrat", sans-serif;
  }
  .bag__handle {
    position: absolute;
    left: 280px;
    top: 64px;
    width: 140px;
    height: 38px;
    border-radius: 19px;
    background: var(--backdrop);
  }
  .brand {
    position: absolute;
    left: 70px;
    top: 230px;
    display: flex;
    align-items: center;
    gap: 26px;
  }
  .brand__square {
    width: 64px;
    height: 64px;
    background: var(--ink);
  }
  .brand__name {
    font-weight: 700;
    font-size: 96px;
    line-height: 1;
    letter-spacing: 0.02em;
  }
  .product {
    position: absolute;
    left: 70px;
    top: 500px;
    right: 60px;
  }
  .product__title {
    margin: 0 0 30px;
    font-weight: 700;
    font-size: 58px;
    letter-spacing: 0.05em;
    line-height: 1;
  }
  .product__size,
  .product__spec {
    margin: 0 0 30px;
    font-weight: 500;
    font-size: 28px;
    letter-spacing: 0.06em;
    line-height: 1.15;
  }
</style>
</head>
<body>
  <main class="canvas">
    <section class="bag">
      <div class="bag__handle"></div>
      <div class="brand">
        <span class="brand__square"></span>
        <span class="brand__name">LUMETRIC</span>
      </div>
      <div class="product">
        <h1 class="product__title">BIAS LIGHTING</h1>
        <p class="product__size">EXTRA LARGE<br>5 METERS</p>
        <p class="product__spec">SIMULATED D65 CRI 90+<br>6500K WHITE BIAS LIGHTING</p>
      </div>
    </section>
  </main>
</body>
</html>
```